Counseling Practice Business Card

I need a professional looking business card incorporating my new logo that was just completed. Card needs to incorporate my name and title, description of my specialty, my address, my phone number, my fax number, my email and my website URL. I need to be able to choose design on/with different paper colors and textures.
I do not have a lot of business card ideas so I am open to anything but I want bold,sharp, clear card without additional designs other than my logo (see attached file info). I am open to different color backgrounds or paper colors including black. I do not like traditional brackets around area codes in phone number or dashes between numbers in phone number. Am open to other ways of presenting including periods between numbers as appropriate. I do not know enough to know what I like yet but I want card to coordinate and work together with my logo. My practice emphasizes natural mental health interventions so any use of color (with background paper color or the blue and green in my logo) that elicits nature is nice. In addition to black, any natural brown or wood looking background might be desirable also. Most of the offerings so far look very similar and boring.

Target Market(s)

Potential therapy clients and other professionals

Contact Information for Business Card

Card information:
Gerald M. Whitcombe, Ph.D.
Licensed Clinical Psychologist
Integrative Health Coach
4812 Marlowe Ridge Blvd SE
Suite 310
Carrow Falls, GA 30487
(770) 415-2983 phone
(770) 581-4096 fax
drgeraldwhitcombe@quillmarsh.net
brightfernwellness.net

Font styles to use
Serif
Sans Serif
Other font styles liked:
• anything that you think looks crisp, clear and easily readable

Requirements
Must have
• Any color used should coordinate with my logo design (see attached files).
• Card should be printed horizontally so top and bottom are longest sides of rectangle.
• Background color or paper color should complement and highlight logo. Do not like a white background. black, grey, brown or any color my logo would blend well with.
Nice to have
• I would like designer to utilize color to highlight letters/name or phone-fax-web symbols.
• Bottom edge of card could be highlighted if appropriate to an idea.
Should not have
• I would NOT want the card to have a pure white background at all.
• No clear cards.
• Cards should be oriented with long sides on bottom and top, NOT sides. DO NOT LIKE THIS THIN TALL ORIENTATION.

```html
<!DOCTYPE html>
<html lang="en">
<head>
<meta charset="utf-8">
<title>Brightfern Wellness – Business Card</title>
<link rel="stylesheet" href="https://fonts.googleapis.com/css2?family=Roboto:wght@400;700&family=Roboto+Condensed:wght@700&display=swap">
<style>
  :root {
    --backdrop: #e8dccd;
    --card-brown: #a97b5d;
    --name-blue: #2b7cc9;
    --title-green: #17783a;
    --address-tint: #d4c2b5;
    --value-ink: #4b3a31;
    --web-tint: #d0bcae;
  }
  * { box-sizing: border-box; margin: 0; padding: 0; }
  html, body {
    width: 1200px;
    height: 960px;
    overflow: hidden;
    background: var(--backdrop);
  }
  .stage {
    position: relative;
    width: 1200px;
    height: 960px;
  }
  .card {
    position: absolute;
    width: 600px;
    height: 342px;
    background: var(--card-brown);
    font-family: "Roboto", Arial, sans-serif;
    text-align: center;
  }
  .card--front { left: 315px; top: 113px; }
  .card--back  { left: 312px; top: 473px; }

  .holder-name {
    position: absolute;
    top: 46px;
    width: 100%;
    font-family: "Roboto Condensed", "Arial Narrow", sans-serif;
    font-weight: 700;
    font-size: 21px;
    color: var(--name-blue);
    text-transform: uppercase;
  }
  .holder-titles {
    position: absolute;
    top: 70px;
    width: 100%;
    font-weight: 700;
    font-size: 15.5px;
    line-height: 19px;
    color: var(--title-green);
  }
  .address {
    position: absolute;
    top: 142px;
    width: 100%;
    font-size: 14px;
    line-height: 18px;
    color: var(--address-tint);
  }
  .contact-list {
    position: absolute;
    top: 216px;
    width: 100%;
    list-style: none;
    font-size: 14px;
    line-height: 19px;
    color: var(--value-ink);
  }
  .contact-label {
    font-weight: 700;
    color: var(--name-blue);
  }

  .practice-name {
    position: absolute;
    top: 132px;
    width: 100%;
    display: flex;
    justify-content: center;
    align-items: center;
    gap: 14px;
    font-weight: 700;
    font-size: 46px;
    color: var(--title-green);
  }
  .practice-dot {
    width: 22px;
    height: 22px;
    border-radius: 50%;
    background: var(--name-blue);
  }
  .practice-web {
    position: absolute;
    top: 283px;
    width: 100%;
    font-size: 14px;
    letter-spacing: 5px;
    color: var(--web-tint);
  }
</style>
</head>
<body>
<main class="stage">
  <section class="card card--front">
    <h1 class="holder-name">Gerald M. Whitcombe, Ph.D.</h1>
    <p class="holder-titles">Licensed Clinical Psychologist<br>Integrative Health Coach</p>
    <p class="address">4812 Marlowe Ridge Blvd SE<br>Suite 310 Carrow Falls, GA 30487</p>
    <ul class="contact-list">
      <li><span class="contact-label">Phone:</span> (770) 415-2983</li>
      <li><span class="contact-label">Fax:</span> (770) 581-4096</li>
      <li><span class="contact-label">Email:</span> drgeraldwhitcombe@quillmarsh.net</li>
      <li><span class="contact-label">Web:</span> www.brightfernwellness.net</li>
    </ul>
  </section>

  <section class="card card--back">
    <div class="practice-name">
      <span class="practice-dot" aria-hidden="true"></span>
      <span>Brightfern Wellness</span>
    </div>
    <p class="practice-web">www.brightfernwellness.net</p>
  </section>
</main>
</body>
</html>
```